Evaporative Air Conditioning Summer Service

Would like to design a flyer to send out in an email to existing clients to promote a Pre-summer service for Evaporative Air Conditioners
Cost will be $110.00 inc gst
Tasks included in service are
- Inspection and clean of pads
- Inspection and check float valve, water pump, fan, motor, bearings, drain
- Clean basin
- Supply of bacterial tablet
- Inspect overall condition of unit
- Any repairs if required will be quoted
Please see files attached of a previous very basic flyer I have used for installation and replacement unit costs. This has current contact information
Have also uploaded company logo for use.
Thanks
Plumbing

```html
<!DOCTYPE html>
<html lang="en">
<head>
<meta charset="utf-8">
<title>Pre-Summer Service – Harbour Gas &amp; Plumbing</title>
<link href="https://fonts.googleapis.com/css2?family=Oswald:wght@600;700&family=Exo+2:ital,wght@0,500;0,600;0,700;1,400&family=Arimo:wght@400&display=swap" rel="stylesheet">
<style>
  :root{
    --backdrop:#7a7a7a;
    --paper:#ffffff;
    --brand-blue:#0d6fb8;
    --deep-blue:#234ea0;
    --orange:#f39021;
    --gold:#f7b21b;
    --ink:#1c1c1c;
    --sky:#a9cdef;
  }
  *{box-sizing:border-box;margin:0;padding:0}
  html,body{width:1200px;height:1200px;overflow:hidden;background:var(--backdrop)}
  .flyer{position:absolute;left:196px;top:30px;width:807px;height:1140px;background:var(--paper);overflow:hidden;font-family:'Arimo',Arial,sans-serif}
  .hero{position:absolute;left:0;top:0;width:807px;height:530px;
    background:linear-gradient(180deg,var(--sky) 0%,#c9dcea 40%,#b7c2c9 62%,#dfe6e1 85%,#ffffff 100%)}
  .brand{position:absolute;left:61px;top:452px;display:flex;align-items:center;gap:12px}
  .brand-dot{width:52px;height:52px;border-radius:50%;background:var(--deep-blue)}
  .brand-name{font-family:'Exo 2',sans-serif;font-weight:700;font-size:30px;color:var(--deep-blue);letter-spacing:.5px}
  .headline{position:absolute;left:56px;top:552px;font-family:'Oswald',sans-serif;font-weight:700;font-size:80px;line-height:1;color:var(--brand-blue);letter-spacing:-1px;white-space:nowrap;transform:scaleX(0.95);transform-origin:left top}
  .subhead{position:absolute;left:56px;top:624px;font-family:'Exo 2',sans-serif;font-weight:600;font-size:45px;color:var(--orange);white-space:nowrap}
  .subhead em{font-weight:400;font-style:italic}
  .includes-tab{position:absolute;left:56px;top:697px;width:190px;height:38px;background:var(--deep-blue);clip-path:polygon(0 0,84% 0,100% 100%,0 100%);
    font-family:'Exo 2',sans-serif;font-weight:600;font-size:24px;color:#fff;padding:4px 0 0 11px}
  .includes-rule{position:absolute;left:56px;top:732px;width:686px;height:3px;background:var(--deep-blue)}
  .task-list{position:absolute;top:752px;list-style:none;font-size:19px;line-height:25px;color:var(--ink)}
  .task-list.left{left:56px;width:290px}
  .task-list.right{left:387px;width:400px}
  .task-list li{position:relative;padding-left:27px}
  .task-list svg{position:absolute;left:0;top:4px}
  .footer-wave{position:absolute;left:0;top:800px}
  .price-badge{position:absolute;left:44px;top:872px;width:246px;height:246px;border-radius:50%;background:#fff;
    display:flex;align-items:center;justify-content:center}
  .price-disc{width:222px;height:222px;border-radius:50%;background:linear-gradient(160deg,#5f9fd8 0%,var(--brand-blue) 45%,var(--deep-blue) 100%);
    display:flex;flex-direction:column;align-items:center;justify-content:center;font-family:'Oswald',sans-serif;font-weight:600;color:#fff;line-height:1}
  .price-amount{font-size:60px;letter-spacing:-1px}
  .price-tax{font-size:44px;margin-top:4px}
  .contact{position:absolute;left:330px;top:970px;width:420px;text-align:center;color:#fff}
  .contact-call{font-family:'Exo 2',sans-serif;font-weight:700;font-size:34px;color:var(--orange);line-height:1}
  .contact-call span{font-weight:500}
  .contact-phone{font-family:'Exo 2',sans-serif;font-weight:600;font-size:58px;line-height:1.1;letter-spacing:3px}
  .contact-email{font-size:17px;margin-top:2px}
  .contact-abn{font-family:'Exo 2',sans-serif;font-size:17px;color:var(--orange);margin-top:10px}
  .contact-abn b{font-weight:700}
</style>
</head>
<body>
<main class="flyer">
  <div class="hero" role="img" aria-label="Photo of a modern two-storey house with evaporative air conditioner units in the foreground"></div>

  <div class="brand">
    <span class="brand-dot"></span>
    <span class="brand-name">HARBOUR GAS &amp; PLUMBING</span>
  </div>

  <h1 class="headline">PRE-SUMMER SERVICE</h1>
  <p class="subhead"><em>for</em> Evaporative Air Conditioners</p>

  <div class="includes-tab">INCLUDES:</div>
  <div class="includes-rule"></div>

  <ul class="task-list left">
    <li><svg width="18" height="18" viewBox="0 0 18 18"><circle cx="9" cy="9" r="9" fill="var(--orange)"/><path d="M5 9.3l2.7 2.6L13 6.5" fill="none" stroke="#fff" stroke-width="2"/></svg>Inspection &amp; clean of pads</li>
    <li><svg width="18" height="18" viewBox="0 0 18 18"><circle cx="9" cy="9" r="9" fill="var(--orange)"/><path d="M5 9.3l2.7 2.6L13 6.5" fill="none" stroke="#fff" stroke-width="2"/></svg>Inspection &amp; check float valve, water pump, fan, motor, bearings, drain</li>
  </ul>
  <ul class="task-list right">
    <li><svg width="18" height="18" viewBox="0 0 18 18"><circle cx="9" cy="9" r="9" fill="var(--orange)"/><path d="M5 9.3l2.7 2.6L13 6.5" fill="none" stroke="#fff" stroke-width="2"/></svg>Clean basin</li>
    <li><svg width="18" height="18" viewBox="0 0 18 18"><circle cx="9" cy="9" r="9" fill="var(--orange)"/><path d="M5 9.3l2.7 2.6L13 6.5" fill="none" stroke="#fff" stroke-width="2"/></svg>Supply of bacterial tablet</li>
    <li><svg width="18" height="18" viewBox="0 0 18 18"><circle cx="9" cy="9" r="9" fill="var(--orange)"/><path d="M5 9.3l2.7 2.6L13 6.5" fill="none" stroke="#fff" stroke-width="2"/></svg>Inspect overall condition of unit</li>
    <li><svg width="18" height="18" viewBox="0 0 18 18"><circle cx="9" cy="9" r="9" fill="var(--orange)"/><path d="M5 9.3l2.7 2.6L13 6.5" fill="none" stroke="#fff" stroke-width="2"/></svg>Any repairs if required will be quoted</li>
  </ul>

  <svg class="footer-wave" width="807" height="340" viewBox="0 0 807 340">
    <defs>
      <linearGradient id="waveBlue" x1="0" x2="1" y1="0" y2="0">
        <stop offset="0" stop-color="var(--deep-blue)"/>
        <stop offset="1" stop-color="var(--brand-blue)"/>
      </linearGradient>
      <linearGradient id="waveSilver" x1="0" x2="1">
        <stop offset="0" stop-color="#555"/>
        <stop offset="0.6" stop-color="#ddd"/>
        <stop offset="1" stop-color="#999"/>
      </linearGradient>
    </defs>
    <path d="M260 160 C420 90 560 50 660 70 C730 82 780 100 807 118" fill="none" stroke="url(#waveSilver)" stroke-width="8"/>
    <path d="M260 172 C420 102 560 62 660 82 C730 94 780 112 807 130" fill="none" stroke="var(--gold)" stroke-width="10"/>
    <path d="M0 200 Q120 230 260 184 C420 114 560 74 660 94 C730 106 780 124 807 142 L807 340 L0 340 Z" fill="url(#waveBlue)"/>
    <path d="M0 196 Q30 204 60 208" fill="none" stroke="var(--orange)" stroke-width="3"/>
  </svg>

  <div class="price-badge">
    <div class="price-disc">
      <span class="price-amount">$110.00</span>
      <span class="price-tax">inc GST</span>
    </div>
  </div>

  <div class="contact">
    <p class="contact-call">CALL US <span>TODAY</span></p>
    <p class="contact-phone">0400555218</p>
    <p class="contact-email">admin@harbourgasplumbing.com.au</p>
    <p class="contact-abn">ABN <b>12345678901</b></p>
  </div>
</main>
</body>
</html>
```